Wholesale in Gold Jewellery & Gold Bullion

We are an established gold jewellery and gold bullion wholesaler selling these products to international clients. We already have a name and logo of our company, hence please view attached current card design. We need a completely new design to compliment our business and industry and the final design should be new and elegant.

Contact Information for Business Card

New card details must be same as per current card. Like logo, name, tel no. & etc.

Colors

Designer to choose colors to be used in the design.

```html
<!DOCTYPE html>
<html lang="en">
<head>
<meta charset="utf-8">
<title>Kestrel &amp; Co Pte Ltd – Business Card</title>
<link rel="stylesheet" href="https://fonts.googleapis.com/css2?family=Oswald:wght@600&family=Open+Sans:wght@400&display=swap">
<style>
  :root {
    --backdrop: #1b1b1b;
    --card: #1e1e1f;
    --card-edge: #262627;
    --gold: #e8a21a;
    --silver: #d9d9d9;
    --muted: #bdbdbd;
    --rule: #4a4a4a;
  }
  * { margin: 0; padding: 0; box-sizing: border-box; }
  html, body {
    width: 1200px; height: 900px; overflow: hidden;
    background: var(--backdrop);
  }
  .stage {
    width: 1200px; height: 900px;
    display: flex; align-items: center; justify-content: center; gap: 40px;
  }
  .card {
    position: relative;
    width: 540px; height: 310px;
    background: linear-gradient(160deg, var(--card-edge), var(--card));
    border-radius: 18px;
    overflow: hidden;
    box-shadow: 0 14px 34px rgba(0,0,0,0.6);
  }
  .wordmark {
    font-family: "Oswald", sans-serif;
    font-weight: 600;
    text-transform: uppercase;
    line-height: 1;
    letter-spacing: 0.5px;
    white-space: nowrap;
  }
  .wordmark .suffix {
    font-size: 0.22em;
    letter-spacing: 1px;
    vertical-align: top;
    margin-left: 4px;
  }
  /* Front */
  .card-front .wordmark {
    position: absolute;
    left: 0; right: 0; top: 50%;
    transform: translateY(-50%);
    text-align: center;
    font-size: 64px;
    color: var(--silver);
  }
  /* Back */
  .card-back .brand {
    position: absolute;
    right: 30px; top: 36px;
    display: flex; align-items: center; gap: 14px;
  }
  .card-back .brand-dot {
    width: 44px; height: 44px; border-radius: 50%;
    background: var(--gold);
  }
  .card-back .wordmark {
    font-size: 40px;
    color: var(--gold);
  }
  .card-back .divider {
    position: absolute;
    left: 30px; right: 30px; top: 116px;
    height: 1px; background: var(--rule);
  }
  .person {
    position: absolute; left: 30px; top: 134px;
    font-family: "Open Sans", sans-serif;
  }
  .person .name {
    font-family: "Oswald", sans-serif;
    font-weight: 600;
    text-transform: uppercase;
    color: var(--gold);
    font-size: 19px;
    line-height: 24px;
    letter-spacing: 0.5px;
  }
  .person .role { color: var(--muted); font-size: 14px; line-height: 20px; margin-bottom: 8px; }
  .contact-list { list-style: none; }
  .contact-list li {
    display: flex; align-items: center; gap: 10px;
    color: var(--muted); font-size: 14px; line-height: 21px;
  }
  .contact-list svg { width: 13px; height: 13px; fill: var(--gold); flex: none; }
  .address {
    position: absolute; right: 30px; top: 136px;
    font-family: "Open Sans", sans-serif;
    font-style: normal;
    color: var(--muted); font-size: 14px; line-height: 19px;
    text-align: right;
  }
</style>
</head>
<body>
<main class="stage">
  <section class="card card-front" aria-label="Card front">
    <div class="wordmark">Kestrel &amp; Co<span class="suffix">Pte Ltd</span></div>
  </section>

  <section class="card card-back" aria-label="Card back">
    <div class="brand">
      <span class="brand-dot"></span>
      <span class="wordmark">Kestrel &amp; Co<span class="suffix">Pte Ltd</span></span>
    </div>
    <div class="divider"></div>

    <div class="person">
      <div class="name">Arjun Meravani</div>
      <div class="role">Director</div>
      <ul class="contact-list">
        <li><svg viewBox="0 0 16 16" aria-label="Telephone"><path d="M1 4c0-2 2-3 7-3s7 1 7 3v2h-4V4.5C9.5 4 6.5 4 5 4.5V6H1zM3 7h10l1 7H2z"/></svg>+65 6100 2400</li>
        <li><svg viewBox="0 0 16 16" aria-label="Mobile"><path d="M4 0h8a1 1 0 0 1 1 1v14a1 1 0 0 1-1 1H4a1 1 0 0 1-1-1V1a1 1 0 0 1 1-1zm1 2v10h6V2zm3 11a1 1 0 1 0 0 2 1 1 0 0 0 0-2z"/></svg>+65 9100 3321</li>
        <li><svg viewBox="0 0 16 16" aria-label="Fax"><path d="M4 0h8v5H4zM1 6h14v7h-3v3H4v-3H1zm4 5v3h6v-3z"/></svg>+65 6100 2411</li>
        <li><svg viewBox="0 0 16 16" aria-label="Email"><path d="M0 3h16v1L8 9 0 4zm0 3l8 5 8-5v7H0z"/></svg>arjun@kestrelco.com</li>
      </ul>
    </div>

    <address class="address">
      12 Lantern Row<br>Singapore 100000
    </address>
  </section>
</main>
</body>
</html>
```